Business card for medical clinic

I need an upmarket, modern medical/health business card for my clinic

Contact Information for Business Card

name, address, email, qr code

```html
<!DOCTYPE html>
<html lang="en">
<head>
<meta charset="utf-8">
<title>Calder Health Partners – Business Card</title>
<link rel="stylesheet" href="https://fonts.googleapis.com/css2?family=Poppins:wght@300;400;500;600;700&display=swap">
<style>
  :root {
    --stage: #232323;
    --card-white: #ffffff;
    --brand-blue: #29a3dc;
    --brand-blue-light: #4fb6e6;
    --emboss-blue: #8fd3f2;
    --ink: #161616;
  }
  * { box-sizing: border-box; margin: 0; padding: 0; }
  html, body {
    width: 1200px;
    height: 780px;
    overflow: hidden;
    background: var(--stage);
    font-family: "Poppins", Arial, sans-serif;
  }
  .stage {
    position: relative;
    width: 1200px;
    height: 780px;
    display: flex;
    align-items: center;
    justify-content: center;
    gap: 40px;
  }
  .card {
    position: relative;
    width: 540px;
    height: 309px;
    box-shadow: 0 10px 30px rgba(0,0,0,.45);
  }

  /* Front side */
  .card--front { background: var(--card-white); }
  .brand {
    position: absolute;
    left: 30px;
    top: 118px;
    display: flex;
    align-items: center;
    gap: 12px;
  }
  .brand__circle {
    width: 56px;
    height: 56px;
    border: 4px solid var(--brand-blue);
    border-radius: 50%;
    flex: none;
  }
  .brand__name {
    color: var(--brand-blue);
    font-weight: 600;
    font-size: 17px;
    line-height: 1.15;
    letter-spacing: .5px;
    text-transform: uppercase;
  }
  .divider {
    position: absolute;
    left: 262px;
    top: 58px;
    width: 1px;
    height: 192px;
    background: var(--brand-blue);
  }
  .contact {
    position: absolute;
    left: 290px;
    top: 52px;
    right: 20px;
  }
  .contact__name {
    font-size: 26px;
    line-height: 1.1;
    color: var(--brand-blue);
    white-space: nowrap;
  }
  .contact__first { font-weight: 700; }
  .contact__last { font-weight: 300; }
  .contact__title {
    font-size: 12px;
    font-weight: 500;
    color: var(--ink);
    margin-top: 2px;
  }
  .contact__address {
    margin-top: 16px;
    font-size: 12px;
    line-height: 1.45;
    color: var(--brand-blue);
  }
  .contact__list {
    list-style: none;
    margin-top: 14px;
    font-size: 12px;
    line-height: 1.55;
    color: var(--ink);
  }
  .contact__list li {
    display: flex;
    align-items: center;
    gap: 8px;
  }
  .contact__icon { width: 12px; height: 12px; flex: none; }

  /* Back side */
  .card--back {
    background: var(--brand-blue);
    display: flex;
    align-items: center;
    justify-content: center;
  }
  .brand--back {
    position: static;
    gap: 18px;
  }
  .brand--back .brand__circle {
    width: 96px;
    height: 96px;
    border: 5px solid var(--emboss-blue);
  }
  .brand--back .brand__name {
    color: var(--emboss-blue);
    font-size: 26px;
  }
</style>
</head>
<body>
<main class="stage">
  <section class="card card--front" aria-label="Business card front">
    <div class="brand">
      <span class="brand__circle"></span>
      <span class="brand__name">Calder Health<br>Partners</span>
    </div>
    <div class="divider"></div>
    <div class="contact">
      <p class="contact__name"><span class="contact__first">Marta</span> <span class="contact__last">Lindqvist</span></p>
      <p class="contact__title">Founder &amp; CEO</p>
      <p class="contact__address">418 Brookfield Ave. Suite 300<br>Denton, TX 76201</p>
      <ul class="contact__list">
        <li>
          <svg class="contact__icon" viewBox="0 0 24 24" aria-hidden="true"><path fill="#29a3dc" d="M6.6 10.8a15.1 15.1 0 0 0 6.6 6.6l2.2-2.2a1 1 0 0 1 1-.25 11.4 11.4 0 0 0 3.6.57 1 1 0 0 1 1 1V20a1 1 0 0 1-1 1A17 17 0 0 1 3 4a1 1 0 0 1 1-1h3.5a1 1 0 0 1 1 1c0 1.25.2 2.45.57 3.57a1 1 0 0 1-.25 1z"/></svg>
          (940) 555-0137
        </li>
        <li>
          <svg class="contact__icon" viewBox="0 0 24 24" aria-hidden="true"><circle cx="12" cy="12" r="10" fill="none" stroke="#29a3dc" stroke-width="2.4"/><path d="M2 12h20M12 2c3 3 3 17 0 20M12 2c-3 3-3 17 0 20" fill="none" stroke="#29a3dc" stroke-width="2"/></svg>
          hello@calderhealth.com
        </li>
        <li>
          <svg class="contact__icon" viewBox="0 0 24 24" aria-hidden="true"><rect x="2" y="5" width="20" height="14" rx="2" fill="#29a3dc"/><path d="M2.5 6l9.5 7 9.5-7" fill="none" stroke="#fff" stroke-width="1.8"/></svg>
          www.calderhealth.com
        </li>
      </ul>
    </div>
  </section>

  <section class="card card--back" aria-label="Business card back">
    <div class="brand brand--back">
      <span class="brand__circle"></span>
      <span class="brand__name">Calder Health<br>Partners</span>
    </div>
  </section>
</main>
</body>
</html>
```